Dynamic Business Card for Sports Supplements Company

Hi! I'm looking for an awesome business card to match my existing sports supplement company. I have uploaded my current company logo and screenshot of the front page of my website.

I would like to have something dynamic and interesting and utilize the colors in the website - the reds and purples

The business card should be double sided and focus on a unique eye-catching design on the back and include all the relevant company info.

Most importantly, it should say somewhere: "Sign up on our website for a coupon code."

Target Market(s)

Mostly for women gym goers but it shouldn't be too feminine. It should be in keeping with the website design. It should flow and clearly be connected to it

Industry/Entity Type

Business

Contact Information for Business Card

Lorraine K. Vestal
CEO
LVestal@Quorvanexco.com
www.quorvanexco.com
555.417.3820
P.O. Box 47315
Fenmore, Ohio 00000

Sign up on our website for a coupon code

Font styles to use
Serif
Sans Serif
Other font styles liked:
• Novecento font family and "Quorvanex" is in AR Destine font

Requirements
Must have
• One side should be a bold Quorvanex logo design. Even just the symbol itself may be o.k. (see attached file)

```html
<!DOCTYPE html>
<html lang="en">
<head>
<meta charset="utf-8">
<title>Quorvanex Business Card</title>
<link href="https://fonts.googleapis.com/css2?family=Open+Sans:ital,wght@0,400;0,600;0,700;1,400&display=swap" rel="stylesheet">
<style>
  :root {
    --backdrop: #5a4a3c;
    --card: #000000;
    --white: #ffffff;
    --red: #ec1c24;
    --grey: #9a9a9a;
    --ink: #111111;
  }
  * { margin: 0; padding: 0; box-sizing: border-box; }
  html, body {
    width: 1200px; height: 987px; overflow: hidden;
    background: var(--backdrop);
    font-family: "Open Sans", Arial, sans-serif;
  }
  .card {
    position: absolute; left: 293px; width: 615px; height: 351px;
    background: var(--card); color: var(--white);
    box-shadow: 0 2px 6px rgba(0,0,0,.35);
  }
  .card--front { top: 130px; }
  .card--back { top: 505px; }

  .name-band {
    position: absolute; left: 0; top: 45px; width: 424px; height: 80px;
    background: var(--white);
  }
  .name-band__name {
    position: absolute; left: 38px; top: 16px;
    font-size: 22px; font-weight: 600; color: var(--red); letter-spacing: .3px;
  }
  .name-band__title {
    position: absolute; left: 39px; top: 45px;
    font-size: 16px; color: var(--ink);
  }
  .accent-block {
    position: absolute; left: 517px; top: 45px; width: 98px; height: 80px;
    background: var(--red);
  }
  .brand {
    position: absolute; left: 364px; top: 134px; width: 214px; text-align: center;
  }
  .brand__name {
    display: block; font-size: 28px; font-weight: 700; letter-spacing: 1px; line-height: 34px;
    color: var(--white);
  }
  .brand__tagline {
    display: block; font-size: 9.5px; letter-spacing: 1.6px; color: var(--grey); margin-top: -1px;
  }
  .address {
    position: absolute; left: 39px; top: 192px; font-size: 15.5px; line-height: 23px;
    font-style: normal;
  }
  .contacts {
    position: absolute; left: 39px; top: 250px; list-style: none; font-size: 15.5px; line-height: 23.5px;
  }
  .contacts li { display: flex; align-items: center; gap: 8px; }
  .contacts svg { width: 15px; height: 15px; flex: none; }

  .back-brand {
    position: absolute; left: 0; right: 0; top: 135px;
    display: flex; justify-content: center; align-items: center; gap: 16px;
  }
  .back-brand__mark { width: 40px; height: 40px; background: var(--red); }
  .back-brand__name {
    font-size: 46px; font-weight: 700; letter-spacing: 2px; color: var(--white);
  }
  .coupon-note {
    position: absolute; left: 0; right: 0; top: 288px; text-align: center;
    font-size: 16px; font-style: italic;
  }
</style>
</head>
<body>
  <section class="card card--front">
    <div class="name-band">
      <div class="name-band__name">LORRAINE K. VESTAL</div>
      <div class="name-band__title">CEO</div>
    </div>
    <div class="accent-block"></div>
    <div class="brand">
      <span class="brand__name">QUORVANEX</span>
      <span class="brand__tagline">YOUR FITNESS COMPANION</span>
    </div>
    <address class="address">
      P.O. Box 47315<br>Fenmore, Ohio 00000
    </address>
    <ul class="contacts">
      <li>
        <svg viewBox="0 0 16 16" aria-hidden="true"><path fill="#ec1c24" d="M3.6 1.5l2.3 2.6-1.3 1.8c.9 2 2.5 3.6 4.5 4.5l1.8-1.3 2.6 2.3-1.4 2.3C7 13.4 2.6 9 1.3 3z"/></svg>
        555.417.3820
      </li>
      <li>
        <svg viewBox="0 0 16 16" aria-hidden="true"><rect x="1" y="3.5" width="14" height="9" fill="#ec1c24"/><path d="M1.5 4l6.5 5 6.5-5" fill="none" stroke="#000" stroke-width="1.2"/></svg>
        LVestal@Quorvanexco.com
      </li>
      <li>
        <svg viewBox="0 0 16 16" aria-hidden="true"><circle cx="8" cy="8" r="6.5" fill="#ec1c24"/><path d="M5 4.5c1.5.5 2 1.5 1.2 2.6-.8 1 .3 2 1.5 2.2M10 11.5c-.5-1.3.3-2.2 1.8-2.3" fill="none" stroke="#000" stroke-width="1.3"/></svg>
        www.quorvanexco.com
      </li>
    </ul>
  </section>

  <section class="card card--back">
    <div class="back-brand">
      <span class="back-brand__mark"></span>
      <span class="back-brand__name">QUORVANEX</span>
    </div>
    <p class="coupon-note">Sign up on our website for a coupon code</p>
  </section>
</body>
</html>
```